BrindleStaffing Business Card Design

We are a staffing company finding positions for dedicated nurses and physicians.

Target Market(s)

Business Professionals

Industry/Entity Type

Staffing

Contact Information for Business Card

Gordon Pratley
Chairman
417 39th Avenue South
SAINT PETERSBURG FL 33712
813-555-4172 Mobile
813-555-8036 Fax
gpratley@brindlestaffing.com
www.brindlestaffing.com

Font styles to use
Sans Serif

Colors
fbee3e
f04a50
f37122

Requirements
Must have
• Logo Attached, see colors below. We'd like to see Yellow, Orange and Red.

```html
<!DOCTYPE html>
<html lang="en">
<head>
<meta charset="utf-8">
<title>BrindleStaffing Business Card</title>
<link rel="stylesheet" href="https://fonts.googleapis.com/css2?family=Source+Sans+3:wght@400;600;700&display=swap">
<style>
  :root {
    --bg: #e6e6e8;
    --card: #ffffff;
    --yellow: #fbee3e;
    --orange: #f37122;
    --red: #f04a50;
    --ink: #1e1e1e;
    --tint: #fef7d2;
  }
  * { margin: 0; padding: 0; box-sizing: border-box; }
  html, body { width: 1200px; height: 1135px; overflow: hidden; }
  body {
    position: relative;
    background: var(--bg);
    font-family: "Source Sans 3", sans-serif;
  }
  .card {
    position: absolute;
    width: 724px;
    height: 413px;
    background: var(--card);
    border-radius: 28px;
    overflow: hidden;
    box-shadow: 0 2px 10px rgba(0,0,0,0.12);
  }
  .card--front { left: 380px; top: 121px; }
  .card--back { left: 66px; top: 591px; }
  .front__waves { position: absolute; left: 0; top: 0; }
  .brand-name {
    position: absolute;
    left: 0; right: 0;
    text-align: center;
    font-weight: 700;
    color: var(--orange);
    letter-spacing: -1px;
    white-space: nowrap;
  }
  .card--front .brand-name { top: 54px; font-size: 56px; }
  .holder {
    position: absolute;
    top: 162px; left: 0; right: 0;
    text-align: center;
    font-size: 29px;
    font-weight: 700;
    color: var(--orange);
  }
  .holder__title { font-weight: 400; color: var(--red); }
  .contact {
    position: absolute;
    left: 0; right: 0;
    display: flex;
    justify-content: center;
    align-items: center;
    gap: 8px;
    font-size: 19px;
    color: var(--ink);
    white-space: nowrap;
  }
  .contact--phone { top: 232px; }
  .contact--web { top: 262px; }
  .contact svg { width: 17px; height: 17px; flex: none; }
  .contact__sep { width: 4px; }
  .address {
    position: absolute;
    bottom: 13px; left: 0; right: 0;
    text-align: center;
    font-size: 19px;
    color: #ffffff;
  }
  .back__panel {
    position: absolute;
    left: 167px; top: 124px;
    width: 414px; height: 166px;
    background: var(--tint);
  }
  .card--back .brand-name { top: 150px; font-size: 64px; }
  .back__url {
    position: absolute;
    top: 250px; left: 0; right: 0;
    text-align: center;
    font-size: 25px;
    letter-spacing: 3px;
    color: var(--ink);
  }
  .back__url b { font-weight: 600; color: var(--orange); }
  .back__url b + b { color: var(--red); }
</style>
</head>
<body>
  <section class="card card--front">
    <svg class="front__waves" width="724" height="413" viewBox="0 0 724 413">
      <path d="M0,268 C180,330 420,370 605,358 C420,368 190,345 0,292 Z" fill="var(--red)"/>
      <path d="M0,298 C210,370 470,388 724,340 L724,413 L0,413 Z" fill="var(--orange)"/>
    </svg>
    <div class="brand-name">BrindleStaffing</div>
    <div class="holder">Gordon Pratley, <span class="holder__title">Chairman</span></div>
    <div class="contact contact--phone">
      <svg viewBox="0 0 20 20"><circle cx="10" cy="10" r="9" fill="none" stroke="var(--ink)" stroke-width="1.5"/><path d="M7,5 L9,8 L8,9 C8.5,10.5 9.5,11.5 11,12 L12,11 L15,13 L13.5,15 C9,14.5 5.5,11 5,6.5 Z" fill="var(--ink)"/></svg>
      <span>813-555-4172</span>
    </div>
    <div class="contact contact--web">
      <svg viewBox="0 0 20 20"><path d="M2,8 L10,3 L18,8 L18,17 L2,17 Z" fill="var(--ink)"/><path d="M2,8 L10,13 L18,8" fill="none" stroke="#fff" stroke-width="1.5"/></svg>
      <span>gpratley@brindlestaffing.com</span>
      <span class="contact__sep"></span>
      <svg viewBox="0 0 20 20" fill="none" stroke="var(--ink)" stroke-width="1.3"><circle cx="10" cy="10" r="8"/><ellipse cx="10" cy="10" rx="3.5" ry="8"/><path d="M2,10 H18 M3.5,6 H16.5 M3.5,14 H16.5"/></svg>
      <span>www.brindlestaffing.com</span>
    </div>
    <div class="address">417 39th Avenue South, Saint Petersburg FL 33712</div>
  </section>

  <section class="card card--back">
    <div class="back__panel"></div>
    <div class="brand-name">BrindleStaffing</div>
    <div class="back__url">www.<b>brindle</b><b>staffing</b>.com</div>
  </section>
</body>
</html>
```